Corporate Business Card

Very professional, Modern, Not to busy, include phone address email, website
(253) 617-4930, 18761 52nd Avenue S, Kent, WA 98047, martin@plumlinegroup.com, varkoworks.com

Target Market(s)

Manufacturing

Industry/Entity Type

Aero, machining, manufacturing, Off road racing

Contact Information for Business Card

Phone, address email, website

```html
<!DOCTYPE html>
<html lang="en">
<head>
<meta charset="utf-8">
<title>Varko Works – Business Card</title>
<link href="https://fonts.googleapis.com/css2?family=Arimo:wght@400;700&display=swap" rel="stylesheet">
<style>
  :root {
    --navy: #173472;
    --red: #d7262c;
    --white: #ffffff;
    --ink: #3a3a3a;
    --page: #1c1c1c;
  }
  * { margin: 0; padding: 0; box-sizing: border-box; }
  html, body { width: 1200px; height: 875px; overflow: hidden; }
  body {
    background: var(--page);
    font-family: "Arimo", Arial, sans-serif;
    display: flex;
    align-items: center;
    justify-content: center;
    gap: 40px;
  }
  .card {
    position: relative;
    width: 540px;
    height: 309px;
    overflow: hidden;
  }

  /* Front */
  .card-front { background: var(--navy); }
  .front-brand {
    position: absolute;
    left: 0; right: 0; top: 108px;
    text-align: center;
    color: var(--white);
    font-weight: 700;
    font-size: 52px;
    letter-spacing: 1px;
  }
  .front-rule {
    position: absolute;
    left: 150px; top: 180px;
    width: 240px; height: 2px;
    background: var(--white);
  }

  /* Back */
  .card-back { background: var(--white); }
  .back-brand {
    position: absolute;
    left: 150px; top: 46px;
    color: var(--navy);
    font-weight: 700;
    font-size: 44px;
    letter-spacing: 1px;
  }
  .back-rule {
    position: absolute;
    left: 150px; top: 104px;
    width: 220px; height: 2px;
    background: var(--navy);
  }
  .person {
    position: absolute;
    left: 40px; top: 150px;
  }
  .person-name {
    color: var(--red);
    font-weight: 700;
    font-size: 24px;
    letter-spacing: 0.5px;
  }
  .person-title {
    color: var(--navy);
    font-size: 15px;
    margin-top: 4px;
    padding-left: 60px;
  }
  .contact {
    position: absolute;
    left: 300px; top: 128px;
    list-style: none;
    color: var(--ink);
    font-size: 12.5px;
    line-height: 1.35;
  }
  .contact li {
    display: flex;
    align-items: flex-start;
    gap: 8px;
    margin-bottom: 6px;
  }
  .contact svg { flex: none; margin-top: 2px; }
  .band { position: absolute; left: 0; bottom: 0; }
  .website {
    position: absolute;
    left: 0; right: 0; bottom: 12px;
    text-align: center;
    color: var(--white);
    font-size: 13px;
    letter-spacing: 3px;
  }
</style>
</head>
<body>
  <section class="card card-front" aria-label="Card front">
    <div class="front-brand">Varko Works</div>
    <div class="front-rule"></div>
  </section>

  <section class="card card-back" aria-label="Card back">
    <div class="back-brand">Varko Works</div>
    <div class="back-rule"></div>

    <div class="person">
      <div class="person-name">DANIEL REYES</div>
      <div class="person-title">Managing Director</div>
    </div>

    <ul class="contact">
      <li>
        <svg width="10" height="13" viewBox="0 0 10 13"><path d="M5 0a5 5 0 0 0-5 5c0 3.5 5 8 5 8s5-4.5 5-8a5 5 0 0 0-5-5zm0 7a2 2 0 1 1 0-4 2 2 0 0 1 0 4z" fill="var(--navy)"/></svg>
        <span>18761 52nd Avenue S<br>Kent, WA 98047</span>
      </li>
      <li>
        <svg width="11" height="11" viewBox="0 0 24 24"><path d="M6.6 10.8a15.1 15.1 0 0 0 6.6 6.6l2.2-2.2a1 1 0 0 1 1-.25 11.4 11.4 0 0 0 3.6.57 1 1 0 0 1 1 1V20a1 1 0 0 1-1 1A17 17 0 0 1 3 4a1 1 0 0 1 1-1h3.5a1 1 0 0 1 1 1c0 1.25.2 2.45.57 3.57a1 1 0 0 1-.25 1z" fill="var(--navy)"/></svg>
        <span>(253) 617-4930</span>
      </li>
      <li>
        <svg width="12" height="9" viewBox="0 0 12 9"><rect width="12" height="9" fill="var(--navy)"/><path d="M0 0l6 5 6-5" stroke="var(--white)" fill="none"/></svg>
        <span>martin@plumlinegroup.com</span>
      </li>
    </ul>

    <svg class="band" width="540" height="309" viewBox="0 0 540 309">
      <polygon points="0,309 0,270 440,270 440,250 432,270 540,270 540,309" fill="var(--navy)"/>
      <polygon points="0,270 420,270 428,232 0,232" fill="none"/>
      <polygon points="0,309 0,268 418,268 418,309" fill="var(--navy)"/>
      <polygon points="418,309 418,268 428,240 540,240 540,309" fill="var(--navy)"/>
      <polygon points="432,240 444,208 540,208 540,240" fill="var(--red)"/>
    </svg>
    <div class="website">WWW.VARKOWORKS.COM</div>
  </section>
</body>
</html>
```